Business Card Design

Online clothing womens clothing store, I sell my clothing online and at the markets.

i would like the attached picture on the front of the card and the contact information on the back.

Industry/Entity Type

Business

Contact Information for Business Card

Marlow Thread
Karen Whitfield
(Instagram symbol) _marlow_thread_
(Facebook symbol) www.fakebookexample.com/marlowthreadau/

W : www.marlowthread.example.au
E : info@marlowthread.example.au
P : 0498716204

```html
<!DOCTYPE html>
<html lang="en">
<head>
<meta charset="utf-8">
<title>Marlow Thread — Business Card</title>
<link href="https://fonts.googleapis.com/css2?family=Open+Sans:wght@400;600;700&display=swap" rel="stylesheet">
<style>
  :root {
    --backdrop: #e8e5e1;
    --card-gap: #f4f4f4;
    --panel-dark: #000000;
    --ink-light: #ffffff;
    --wash-light: #dfe3e2;
    --wash-teal: #8fa6a3;
    --wash-slate: #4d5458;
    --wash-deep: #2c3034;
  }
  * { margin: 0; padding: 0; box-sizing: border-box; }
  html, body {
    width: 1200px;
    height: 900px;
    overflow: hidden;
    background: var(--backdrop);
    font-family: "Open Sans", Arial, sans-serif;
  }
  .card {
    position: absolute;
    left: 145px;
    top: 168px;
    width: 910px;
    height: 564px;
    background: var(--card-gap);
    box-shadow: 0 10px 30px rgba(0,0,0,0.18);
  }
  .card-artwork {
    position: absolute;
    left: 0;
    top: 0;
    width: 482px;
    height: 564px;
    overflow: hidden;
    background:
      radial-gradient(ellipse 55% 45% at 70% 35%, var(--wash-slate) 0%, rgba(77,84,88,0) 70%),
      radial-gradient(ellipse 50% 40% at 40% 85%, var(--wash-deep) 0%, rgba(44,48,52,0) 75%),
      radial-gradient(ellipse 60% 50% at 45% 20%, var(--wash-teal) 0%, rgba(143,166,163,0) 70%),
      linear-gradient(160deg, var(--wash-light) 0%, var(--wash-teal) 45%, var(--wash-slate) 100%);
  }
  .brand-name {
    position: absolute;
    left: 24px;
    right: 24px;
    bottom: 38px;
    color: var(--ink-light);
    font-size: 44px;
    font-weight: 600;
    letter-spacing: 1px;
    line-height: 1;
    white-space: nowrap;
  }
  .card-contact {
    position: absolute;
    left: 497px;
    top: 0;
    width: 413px;
    height: 564px;
    background: var(--panel-dark);
    color: var(--ink-light);
  }
  .holder-name {
    position: absolute;
    right: 48px;
    top: 86px;
    font-size: 35px;
    font-weight: 700;
    line-height: 1.2;
    white-space: nowrap;
  }
  .contact-line {
    position: absolute;
    right: 46px;
    display: flex;
    align-items: center;
    gap: 13px;
    font-size: 21px;
    line-height: 1;
    white-space: nowrap;
  }
  .contact-line .icon {
    width: 24px;
    height: 24px;
    background: var(--ink-light);
    border-radius: 3px;
    display: flex;
    align-items: center;
    justify-content: center;
    flex: none;
  }
  .contact-line .icon svg { width: 16px; height: 16px; }
  .contact-line .icon-plain {
    width: 20px;
    height: 20px;
    margin: 0 2px;
    border-radius: 2px;
    background: var(--ink-light);
    flex: none;
  }
  .line-phone { top: 220px; }
  .line-email { top: 258px; }
  .line-web { top: 295px; }
  .line-instagram { top: 403px; }
  .line-facebook { top: 439px; }
</style>
</head>
<body>
  <div class="card">
    <div class="card-artwork" role="img" aria-label="Abstract watercolour painting in misty grey, teal and slate tones">
      <span class="brand-name">MARLOW THREAD</span>
    </div>

    <div class="card-contact">
      <div class="holder-name">Karen Whitfield</div>

      <div class="contact-line line-phone">
        <span>0498716204</span>
        <span class="icon">
          <svg viewBox="0 0 16 16"><path d="M4.2 1.5 6 4.6 4.8 6a8.5 8.5 0 0 0 5.2 5.2l1.4-1.2 3.1 1.8-.9 2.6c-.2.5-.7.7-1.2.6C6.8 14 2 9.2 1 3.6c-.1-.5.1-1 .6-1.2z" fill="#000"/></svg>
        </span>
      </div>

      <div class="contact-line line-email">
        <span>info@marlowthread.example.au</span>
        <span class="icon">
          <svg viewBox="0 0 16 16"><rect x="1.5" y="3.5" width="13" height="9" fill="#000"/><path d="M1.5 3.5 8 9l6.5-5.5" fill="none" stroke="#fff" stroke-width="1.2"/></svg>
        </span>
      </div>

      <div class="contact-line line-web">
        <span>www.marlowthread.example.au</span>
        <span class="icon">
          <svg viewBox="0 0 16 16" fill="none" stroke="#000" stroke-width="1.8" stroke-linecap="round"><path d="M7 9.5 9.5 7"/><path d="M6.2 7.3 4.4 9.1a2 2 0 0 0 2.8 2.8L9 10.1"/><path d="M9.8 8.7l1.8-1.8a2 2 0 0 0-2.8-2.8L7 5.9"/></svg>
        </span>
      </div>

      <div class="contact-line line-instagram">
        <span>_marlow_thread_</span>
        <span class="icon-plain" aria-hidden="true"></span>
      </div>

      <div class="contact-line line-facebook">
        <span>/marlowthreadau/</span>
        <span class="icon-plain" aria-hidden="true"></span>
      </div>
    </div>
  </div>
</body>
</html>
```